Business Card for Coastal Tundrabridge Advisory

We need a business card for Coastal Tundrabridge Advisory. The company website address is provided below. The company logo is attached. We provide specialized permafrost services to the mining, transportation, and oil & gas industries. The card should be prepared for:
Matthias Korhonen, PhD.
Coastal Tundrabridge Advisory
PO Box 418259
Quillwater, Alaska 99642
Direct: +1-907-555-0143
Email: mkorhonen@tundrabridgeadvisory.example
Website: www.coastaltundrabridgeadvisory.example

```html
<!DOCTYPE html>
<html lang="en">
<head>
<meta charset="utf-8">
<title>Coastal Tundrabridge Advisory — Business Card</title>
<link rel="stylesheet" href="https://fonts.googleapis.com/css2?family=Roboto:wght@300;400;500;700&display=swap">
<style>
  :root {
    --backdrop: #262626;
    --card: #111722;
    --ink: #ffffff;
    --ink-soft: #d9dde4;
    --tone-deep: #0f1520;
    --tone-mid: #16263a;
    --tone-blue: #24557a;
  }
  * { box-sizing: border-box; margin: 0; padding: 0; }
  html, body { width: 1200px; height: 780px; overflow: hidden; }
  body {
    background: var(--backdrop);
    font-family: "Roboto", Arial, sans-serif;
    color: var(--ink);
    display: flex;
    align-items: center;
    justify-content: center;
    gap: 24px;
  }
  .card {
    position: relative;
    width: 548px;
    height: 313px;
    background: var(--card);
    box-shadow: 0 18px 40px rgba(0,0,0,.55);
    overflow: hidden;
  }

  /* Front */
  .brand {
    position: absolute;
    top: 30px;
    right: 30px;
    text-align: right;
    font-weight: 500;
    font-size: 19px;
    letter-spacing: 0.06em;
    text-transform: uppercase;
    line-height: 1.2;
    max-width: 260px;
  }
  .name-bar {
    position: absolute;
    left: 0;
    top: 118px;
    width: 16px;
    height: 44px;
    background: var(--ink);
  }
  .person {
    position: absolute;
    left: 32px;
    top: 112px;
  }
  .person-name { font-size: 30px; line-height: 1.05; font-weight: 400; }
  .person-name .first { font-weight: 700; }
  .person-name .last { font-weight: 300; }
  .person-title { font-size: 17px; font-weight: 500; margin-top: 2px; }

  .address {
    position: absolute;
    left: 32px;
    bottom: 26px;
    font-size: 12.5px;
    font-style: normal;
    line-height: 1.55;
    color: var(--ink-soft);
  }
  .contacts {
    position: absolute;
    right: 22px;
    bottom: 26px;
    list-style: none;
    font-size: 11.5px;
    line-height: 1.55;
    color: var(--ink-soft);
  }
  .contacts li { display: flex; align-items: center; justify-content: flex-end; gap: 7px; }
  .contacts svg { width: 11px; height: 11px; flex: none; }

  /* Back */
  .pattern-area {
    position: absolute;
    inset: 0;
    background:
      radial-gradient(ellipse 60% 80% at 30% 35%, rgba(36,85,122,.55), transparent 70%),
      linear-gradient(160deg, var(--tone-mid) 0%, var(--tone-deep) 70%);
  }
  .back-brand {
    position: absolute;
    top: 68px;
    right: 96px;
    display: flex;
    align-items: center;
    gap: 7px;
    font-size: 13px;
    font-weight: 500;
    letter-spacing: 0.06em;
    text-transform: uppercase;
  }
  .back-brand .mark { width: 9px; height: 9px; background: var(--ink); }
  .services {
    position: absolute;
    left: 24px;
    right: 24px;
    bottom: 24px;
    text-align: center;
  }
  .services h2 { font-size: 12.5px; font-weight: 700; letter-spacing: 0.02em; margin-bottom: 4px; }
  .services p { font-size: 11.5px; color: var(--ink-soft); }
</style>
</head>
<body>

  <section class="card card-front" aria-label="Business card front">
    <div class="brand">Coastal Tundrabridge Advisory</div>

    <div class="name-bar"></div>
    <div class="person">
      <h1 class="person-name"><span class="first">Matthias</span> <span class="last">Korhonen</span></h1>
      <p class="person-title">PhD</p>
    </div>

    <address class="address">
      PO Box 418259<br>
      Quillwater, Alaska 99642
    </address>

    <ul class="contacts">
      <li>+1-907-555-0143
        <svg viewBox="0 0 12 12" aria-hidden="true"><path d="M2.5 1h2l1 2.6-1.3.9a6 6 0 0 0 3.3 3.3l.9-1.3 2.6 1v2a1 1 0 0 1-1 1A9.5 9.5 0 0 1 1.5 2a1 1 0 0 1 1-1z" fill="#fff"/></svg>
      </li>
      <li>mkorhonen@tundrabridgeadvisory.example
        <svg viewBox="0 0 12 12" aria-hidden="true"><rect x="1" y="2.5" width="10" height="7" rx="1" fill="#fff"/><path d="M1.5 3l4.5 3.5L10.5 3" stroke="#111722" stroke-width="1" fill="none"/></svg>
      </li>
      <li>www.coastaltundrabridgeadvisory.example
        <svg viewBox="0 0 12 12" aria-hidden="true"><circle cx="6" cy="6" r="5" fill="#fff"/><path d="M1 6h10M6 1c-2.2 2.8-2.2 7.2 0 10M6 1c2.2 2.8 2.2 7.2 0 10" stroke="#111722" stroke-width=".8" fill="none"/></svg>
      </li>
    </ul>
  </section>

  <section class="card card-back" aria-label="Business card back">
    <div class="pattern-area" role="img" aria-label="Decorative brand pattern area in dark navy with a soft blue glow"></div>

    <div class="back-brand"><span class="mark"></span>Coastal Tundrabridge Advisory</div>

    <div class="services">
      <h2>OUR SERVICES</h2>
      <p>We provide specialized permafrost services to the mining, transportation, and oil &amp; gas industries</p>
    </div>
  </section>

</body>
</html>
```